Photographer's price list

I am a photographer who runs a studio (Marrowfield Studio) and need to have a document to send clients detailing my packages (collections) and prices. I have written the text in a word document and need a designer to lay it out for me using my logo and two specific fonts: DejaVu Sans and LainieDaySH.

The look should be clean and modern and keep in the same style as my logo. I will primarily be using the final product as a PDF file to email to potential clients. It should stay black and white.

I would also like to be able to update the text myself as my prices and packages change. So I would like a PSD file.

I think I would like for the document to be in landscape format with "Collections" on one side and A la Carte on the other, but I am open to other ideas.

As for sizing, it should be a standard size so that clients can print it out if they like.

Industry/Entity Type

Landscape

Requirements
Must have
• my logo
fonts: DejaVu and LainieDaySH
Easy to email
Easy to display on one page upon opening
Standard size so that printing from a home computer is easy to do.

```html
<!DOCTYPE html>
<html lang="en">
<head>
<meta charset="utf-8">
<title>Marrowfield Studio – 2013 Photography Collections</title>
<link rel="stylesheet" href="https://fonts.googleapis.com/css2?family=Saira+Condensed:wght@200;300;400&display=swap">
<style>
  :root {
    --black: #050505;
    --white: #ffffff;
    --stage: #e6e6e6;
    --grey-head: #a9a9a9;
    --grey-text: #9a9a9a;
    --ink: #2a2a2a;
    --ink-soft: #6b6b6b;
    --rainbow: linear-gradient(90deg, #2aa38f, #3b8fd0, #6b4db8, #c43b7a, #e5332a, #f08a24, #f6d32a, #8cc63f, #2aa38f, #2a6fb5);
  }
  * { box-sizing: border-box; margin: 0; padding: 0; }
  html, body { width: 1200px; height: 849px; overflow: hidden; }
  body {
    background: var(--stage);
    font-family: "Saira Condensed", "Arial Narrow", sans-serif;
    position: relative;
  }
  .spread {
    position: absolute;
    left: 64px;
    width: 1072px;
    height: 378px;
    display: flex;
    box-shadow: 0 2px 8px rgba(0,0,0,.25);
  }
  .spread--outer { top: 22px; }
  .spread--inner { top: 442px; }
  .page { position: relative; width: 536px; height: 378px; overflow: hidden; }
  .abs { position: absolute; }

  .heading {
    font-weight: 200;
    text-transform: uppercase;
    color: var(--grey-head);
    line-height: 1.2;
  }
  .copy { font-size: 7px; line-height: 1.55; font-weight: 300; color: var(--grey-text); }
  .copy--dark { color: var(--ink-soft); }
  .rainbow { position: absolute; left: 0; right: 0; bottom: 0; height: 4px; background: var(--rainbow); }

  /* Studio name mark: plain text with one small plain circle */
  .studio-mark {
    position: absolute;
    display: flex; align-items: center; gap: 7px;
  }
  .studio-mark__dot { width: 9px; height: 9px; border-radius: 50%; background: var(--black); flex: none; }
  .studio-mark__name { font-size: 14px; font-weight: 300; letter-spacing: 2px; color: var(--black); white-space: nowrap; }

  /* Back page */
  .back { background: var(--white); }
  .back__top { position: absolute; left: 0; top: 0; width: 100%; height: 188px; background: var(--black); }
  .back__title { left: 44px; top: 40px; font-size: 19px; }
  .back__about { left: 44px; top: 74px; width: 340px; color: #d6d6d6; }
  .back__about p + p { margin-top: 8px; }
  .back__mark { left: 0; width: 100%; top: 258px; justify-content: center; }
  .back__url { left: 0; width: 100%; top: 340px; text-align: center; font-size: 8px; letter-spacing: 2px; color: var(--ink); }

  /* Cover */
  .cover { background: var(--black); }
  .cover__top { position: absolute; left: 0; top: 0; width: 100%; height: 188px; background: var(--white); }
  .cover__title { left: 190px; top: 20px; font-size: 22px; letter-spacing: 2px; color: #5a5a5a; font-weight: 300; }
  .cover__mark { left: 26px; top: 158px; }
  .cover__mark .studio-mark__name { font-size: 13px; letter-spacing: 1.5px; }
  .cover__photo {
    left: 193px; top: 55px; width: 306px; height: 257px;
    background: linear-gradient(180deg, #4c6a3c 0%, #7a7a6e 35%, #b9a99a 55%, #8c8c8c 75%, #6d6d6d 100%);
  }
  .cover__call { right: 36px; top: 322px; font-size: 22px; letter-spacing: 2.5px; color: #d9d9d9; font-weight: 300; }

  /* Inner page 1 */
  .inner1 { background: var(--black); }
  .inner1__lead { left: 34px; top: 26px; width: 450px; font-size: 19px; }
  .inner1__intro { left: 34px; top: 95px; width: 230px; }
  .inner1__band { left: 0; top: 191px; width: 536px; height: 183px; background: #0d0d0d; }
  .inner1__photo {
    left: 250px; top: 191px; width: 286px; height: 183px;
    background: radial-gradient(ellipse at 55% 45%, #9a9a9a 0%, #4a4a4a 45%, #0d0d0d 80%);
  }
  .collection__title { font-size: 19px; }
  .col1 { left: 34px; top: 168px; width: 206px; }
  .col2 { left: 34px; top: 244px; width: 206px; }
  .col1 .copy, .col2 .copy { margin-top: 6px; }

  /* Inner page 2 */
  .inner2 { background: var(--white); }
  .inner2__dark { position: absolute; left: 0; top: 0; width: 268px; height: 100%; background: var(--black); }
  .col3 { left: 38px; top: 26px; width: 216px; }
  .col4 { left: 38px; top: 104px; width: 216px; }
  .col3 .copy, .col4 .copy { margin-top: 6px; }
  .alacarte-intro { left: 40px; top: 222px; width: 210px; }
  .alacarte-intro .copy { margin-top: 4px; }
  .alacarte-digital { left: 40px; top: 300px; width: 210px; }
  .alacarte-digital .copy { margin-top: 8px; }
  .sub-title { font-size: 15px; }

  .menu { left: 283px; top: 30px; width: 232px; }
  .menu__item + .menu__item { margin-top: 10px; }
  .menu__title { font-size: 13px; font-weight: 300; color: #555; text-transform: uppercase; line-height: 1.15; }
  .menu__item .copy { margin-top: 3px; }
</style>
</head>
<body>

<section class="spread spread--outer">
  <article class="page back">
    <div class="back__top"></div>
    <h2 class="abs heading back__title">About us</h2>
    <div class="abs copy back__about">
      <p>Marrowfield Studio, based in Leipzig, Germany, is a newly launched studio led by American photographer, Clara Whitcombe Marrow. She specializes in portrait, children and cause-related photography, and is currently working on a collection featuring mothers and children.</p>
      <p>Clara holds a Master's in Foreign Service and International Development from Harwell University, and a BA from Linden College. She is available for assignments worldwide</p>
      <p>CLARA Whitcombe<br>Leipzig, 04109, Germany</p>
    </div>
    <div class="studio-mark back__mark"><span class="studio-mark__dot"></span><span class="studio-mark__name">MARROWFIELD STUDIO</span></div>
    <p class="abs back__url">www.marrowfieldstudio.com</p>
    <div class="rainbow"></div>
  </article>

  <article class="page cover">
    <div class="cover__top"></div>
    <h1 class="abs cover__title">2013 PHOTOGRAPHY COLLECTIONS</h1>
    <div class="studio-mark cover__mark"><span class="studio-mark__dot"></span><span class="studio-mark__name">MARROWFIELD STUDIO</span></div>
    <div class="abs cover__photo" role="img" aria-label="Portrait of a young woman in a red hood, hands framing her face"></div>
    <p class="abs cover__call">CALL NOW: 0402 555 180</p>
  </article>
</section>

<section class="spread spread--inner">
  <article class="page inner1">
    <h2 class="abs heading inner1__lead">One to two hour portrait session with photographer in location of your choice (unlimited time if necessary!)</h2>
    <p class="abs copy inner1__intro">Clara will create a presentation video with hand-selected music and custom editing, which tells your story, highlights the best images, and reveals the connections within your family. An online gallery for viewing and ordering helps you share your images with family and friends.</p>
    <div class="abs inner1__band"></div>
    <div class="abs inner1__photo" role="img" aria-label="Black and white portrait of a woman"></div>
    <div class="abs col1">
      <h3 class="heading collection__title">Collection 1 [ 300 € ]</h3>
      <p class="copy">Your favorite five images from the session will be professionally edited and presented to you on disk as high resolution jpegs</p>
    </div>
    <div class="abs col2">
      <h3 class="heading collection__title">Collection 2 [ 400 € ]</h3>
      <p class="copy">Your favorite ten images from the session will be professionally edited and given to you on disk as high resolution jpegs.<br>Your favorite image from the session will be professionally printed for you (20x30cm) on Vellmark paper, Clara's favorite for portraits.</p>
    </div>
    <div class="rainbow"></div>
  </article>

  <article class="page inner2">
    <div class="inner2__dark"></div>
    <div class="abs col3">
      <h3 class="heading collection__title">Collection 3 [ 500 € ]</h3>
      <p class="copy">Your favorite fifteen images from the session will be professionally edited and presented to you on disk as high resolution jpegs. Your favorite two images from the session will be professionally printed for you (20x30cm) on Vellmark paper, Clara's favorite for portraits.</p>
    </div>
    <div class="abs col4">
      <h3 class="heading collection__title">Collection 4 [ 600 € ]</h3>
      <p class="copy">ALL presented images from the session will be professionally edited and presented to you on disk as high resolution jpegs (approximately 40+ images). Your favorite two images from the session will be professionally printed for you 20x30cm) on Vellmark paper, Clara's favorite for portraits.</p>
    </div>
    <div class="abs alacarte-intro">
      <h3 class="heading collection__title">A la carte</h3>
      <p class="copy">These products may be purchased separately to complement your collection. A consultation with Clara will help you decide which products are best for gifts and for your home.</p>
    </div>
    <div class="abs alacarte-digital">
      <h3 class="heading sub-title">A la carte - 25 € each<br>High resolution digital images</h3>
      <p class="copy">Perfect if you just need to add "one more image" to your collection!<br>High-resolution jpeg file</p>
    </div>

    <div class="abs menu">
      <div class="menu__item">
        <h4 class="menu__title">A la carte - 25 € &nbsp;Matt prints</h4>
        <p class="copy copy--dark">Each print is professionally edited, printed on archival photo paper. Purchase includes the JPEG file for your personal digital use. 20x30 cm and Smaller</p>
      </div>
      <div class="menu__item">
        <h4 class="menu__title">A la carte - 45 € &nbsp;Vellmark prints</h4>
        <p class="copy copy--dark">Prints on Vellmark (watercolor) paper are Clara's favorite for large format color prints 30x40 cm</p>
      </div>
      <div class="menu__item">
        <h4 class="menu__title">A la carte - 100 € &nbsp;Canvas prints</h4>
        <p class="copy copy--dark">Ready-to-hang, stretched canvas wall art of your favorite images 30x40 cm</p>
      </div>
      <div class="menu__item">
        <h4 class="menu__title">A la carte - 350 € &nbsp;Framed + matted prints</h4>
        <p class="copy copy--dark">Beautiful Vellmark prints finished with wide mats and simple, elegant frames of your choice 30x40 inch</p>
      </div>
      <div class="menu__item">
        <h4 class="menu__title">Prices begin at - 100 €<br>Custom designed albums</h4>
        <p class="copy copy--dark">Images from your session are selected for the custom design of an album and bound in a book for a modern presentation of your images. There are a number of cover choices for the classic flush-mount and beautifully crafted albums. A great way to display all of your favorite images from your session on your coffee table.</p>
      </div>
    </div>
  </article>
</section>

</body>
</html>
```